Website for BrightlineLabs presentation

We need a new website, ideally as a wordpress there, for BrightlineLabs - we focus on machine learning, big data, data science and data analytics. This website should have two main sections - team presentation, introduction and offered services as static pages, and a blog section.

Target Market(s)

Companies which would like to hire the consultants for data science

Industry/Entity Type

Data Service

Font styles to use
Sans Serif

Colors

Designer to choose colors to be used in the design.

Requirements
Must have
• Wordpress template, blog and presentation pages, nice background images, incorporate the existing logo from brief
Nice to have
• match the word and ppt existing templates for brightline labs

```html
<!DOCTYPE html>
<html lang="en">
<head>
<meta charset="utf-8">
<title>BrightlineLabs</title>
<link href="https://fonts.googleapis.com/css2?family=Open+Sans:wght@400;600;700&family=Signika:wght@600;700&display=swap" rel="stylesheet">
<style>
  :root {
    --brand: #1589c6;
    --brand-dark: #1478b0;
    --text: #5a5a5a;
    --heading-dark: #4a4a4a;
    --panel: #f2f2f2;
    --white: #ffffff;
    --line: #cfcfcf;
  }
  * { box-sizing: border-box; margin: 0; padding: 0; }
  html, body { width: 1200px; height: 2449px; overflow: hidden; }
  body { position: relative; background: var(--white); font-family: "Open Sans", sans-serif; color: var(--text); }
  .abs { position: absolute; }
  .section-title { position: absolute; left: 0; width: 1200px; text-align: center; font-family: "Signika", sans-serif; font-weight: 700; font-size: 38px; color: var(--brand); line-height: 1; }

  .hero-photo { left: 0; top: 0; width: 1200px; height: 604px; background: linear-gradient(100deg, #d5dde6 0%, #eef1f4 35%, #f4f5f7 55%, #dfe4ea 80%, #ccd6e0 100%); }
  .brand-mark { left: 0; top: 250px; width: 1200px; display: flex; justify-content: center; align-items: center; gap: 16px; }
  .brand-dot { width: 22px; height: 22px; border-radius: 50%; background: var(--brand); }
  .brand-name { font-family: "Signika", sans-serif; font-weight: 700; font-size: 58px; color: var(--brand); line-height: 1; }

  .main-nav { left: 0; top: 604px; width: 1200px; height: 52px; background: var(--brand); }
  .nav-link { position: absolute; top: 0; height: 52px; line-height: 52px; font-size: 16px; color: var(--white); text-transform: uppercase; }
  .nav-link.active::after { content: ""; position: absolute; left: -10px; right: -10px; bottom: 0; height: 3px; background: var(--white); }
  .nav-cta { position: absolute; left: 934px; top: 5px; width: 188px; height: 42px; border-radius: 21px; background: var(--white); color: var(--brand); font-weight: 700; font-size: 19px; line-height: 42px; text-align: center; }

  .about-text { left: 207px; width: 788px; text-align: center; font-size: 14px; line-height: 26px; }
  .outline-btn { position: absolute; border: 2px solid var(--brand); border-radius: 24px; color: var(--brand); font-family: "Signika", sans-serif; font-weight: 600; font-size: 20px; text-align: center; }

  .services { left: 0; top: 1063px; width: 1200px; height: 407px; background: var(--panel); }
  .service { position: absolute; width: 260px; margin-left: -130px; text-align: center; top: 1179px; }
  .service-icon { width: 114px; height: 114px; border-radius: 50%; background: var(--brand); margin: 0 auto; display: flex; align-items: center; justify-content: center; }
  .service-name { margin-top: 24px; font-weight: 600; font-size: 24px; color: var(--heading-dark); }
  .service-text { margin-top: 10px; font-size: 14px; line-height: 26px; }

  .blog-card { top: 1587px; width: 500px; height: 291px; }
  .blog-card .blog-photo { position: absolute; inset: 0; }
  .blog-card .blog-caption { position: absolute; left: 24px; top: 194px; width: 440px; font-weight: 700; font-size: 19px; line-height: 31px; color: var(--white); }

  .contact { left: 0; top: 1981px; width: 1200px; height: 405px; background: var(--panel); }
  .field { position: absolute; border-bottom: 1px solid var(--line); font-size: 14px; color: #9a9a9a; padding-bottom: 14px; }

  .site-footer { left: 0; top: 2386px; width: 1200px; height: 63px; background: var(--brand); color: var(--white); font-size: 14px; text-align: center; line-height: 63px; }
</style>
</head>
<body>

<header>
  <div class="abs hero-photo" role="img" aria-label="Photo of a team of consultants talking in a bright office"></div>
  <div class="abs brand-mark"><span class="brand-dot"></span><span class="brand-name">BrightlineLabs</span></div>
  <nav class="abs main-nav">
    <span class="nav-link active" style="left:87px">Home</span>
    <span class="nav-link" style="left:172px">About</span>
    <span class="nav-link" style="left:264px">Services</span>
    <span class="nav-link" style="left:371px">Blog</span>
    <span class="nav-link" style="left:450px">Contact</span>
    <span class="nav-cta">CONTACT US</span>
  </nav>
</header>

<section class="about">
  <h2 class="section-title" style="top:722px">ABOUT US</h2>
  <p class="abs about-text" style="top:773px">Lorem Ipsum is simply dummy text of the printing and typesetting industry. Lorem Ipsum has been the industry's standard dummy text ever since the 1500s, when an unknown printer took a galley of type and scrambled it to make a type specimen book. It has survived not only five centuries, but also the leap into electronic typesetting.</p>
  <p class="abs about-text" style="top:860px">Lorem Ipsum is simply dummy text of the printing and typesetting industry. Lorem Ipsum has been the industry's standard dummy text ever since the 1500s, when an unknown printer took a galley of type and scrambled.</p>
  <span class="outline-btn" style="left:506px;top:936px;width:188px;height:45px;line-height:41px">KNOW MORE</span>
</section>

<section class="abs services"></section>
<h2 class="section-title" style="top:1117px">OUR SERVICES</h2>
<div class="service" style="left:198px">
  <div class="service-icon">
    <svg width="56" height="56" viewBox="0 0 56 56" fill="none" stroke="#fff" stroke-width="3">
      <circle cx="22" cy="24" r="9"/><circle cx="22" cy="24" r="3"/>
      <path d="M22 11v-4M22 41v-4M9 24H5M39 24h-4M13 15l-3-3M34 36l-3-3M13 33l-3 3M34 12l-3 3"/>
      <circle cx="40" cy="40" r="6"/><path d="M40 31v3M40 46v3M31 40h3M46 40h3"/>
    </svg>
  </div>
  <div class="service-name">Machine learning</div>
  <div class="service-text">Lorem ipsum dolor sit amet,<br>consectetur adipiscing elit.</div>
</div>
<div class="service" style="left:465px">
  <div class="service-icon">
    <svg width="52" height="52" viewBox="0 0 52 52" fill="#fff">
      <rect x="8" y="34" width="7" height="12"/><rect x="18" y="28" width="7" height="18"/><rect x="28" y="31" width="7" height="15"/><rect x="38" y="22" width="7" height="24"/>
      <polyline points="11,22 21,12 31,18 42,6" fill="none" stroke="#fff" stroke-width="2.5"/>
      <circle cx="11" cy="22" r="3"/><circle cx="21" cy="12" r="3"/><circle cx="31" cy="18" r="3"/><circle cx="42" cy="6" r="3"/>
    </svg>
  </div>
  <div class="service-name">Big data</div>
  <div class="service-text">Lorem ipsum dolor sit amet,<br>consectetur adipiscing elit.</div>
</div>
<div class="service" style="left:730px">
  <div class="service-icon">
    <svg width="52" height="52" viewBox="0 0 52 52" fill="none" stroke="#fff" stroke-width="2.5">
      <ellipse cx="26" cy="26" rx="21" ry="8"/><ellipse cx="26" cy="26" rx="21" ry="8" transform="rotate(60 26 26)"/><ellipse cx="26" cy="26" rx="21" ry="8" transform="rotate(-60 26 26)"/>
      <circle cx="26" cy="26" r="4" fill="#fff"/>
    </svg>
  </div>
  <div class="service-name">Data science</div>
  <div class="service-text">Lorem ipsum dolor sit amet,<br>consectetur adipiscing elit.</div>
</div>
<div class="service" style="left:1001px">
  <div class="service-icon">
    <svg width="54" height="54" viewBox="0 0 54 54" fill="none" stroke="#fff" stroke-width="3">
      <circle cx="22" cy="24" r="14"/><path d="M32 34l14 14"/>
      <polyline points="13,29 19,21 24,26 32,15" stroke-width="2.5"/><path d="M34 6l8-2-2 8M42 4l-8 8" stroke-width="2.5"/>
    </svg>
  </div>
  <div class="service-name">Data analytics</div>
  <div class="service-text">Lorem ipsum dolor sit amet,<br>consectetur adipiscing elit.</div>
</div>

<section class="blog">
  <h2 class="section-title" style="top:1523px">LATEST BLOG</h2>
  <article class="abs blog-card" style="left:77px">
    <div class="blog-photo" role="img" aria-label="Photo of business people meeting by an office window" style="background:linear-gradient(180deg,#8fb7c4 0%,#5d7886 45%,#27313c 100%)"></div>
    <p class="blog-caption">Lorem Ipsum is simply dummy text of the printing and typesetting industry.</p>
  </article>
  <article class="abs blog-card" style="left:622px">
    <div class="blog-photo" role="img" aria-label="Photo of a presenter speaking to colleagues in a meeting room" style="background:linear-gradient(180deg,#b9c4cc 0%,#6c7884 45%,#222a33 100%)"></div>
    <p class="blog-caption">Lorem Ipsum is simply dummy text of the printing and typesetting industry.</p>
  </article>
</section>

<section class="abs contact"></section>
<h2 class="section-title" style="top:2034px">CONTACT US</h2>
<div class="field" style="left:131px;top:2115px;width:292px">Name</div>
<div class="field" style="left:452px;top:2115px;width:293px">Email</div>
<div class="field" style="left:776px;top:2115px;width:294px">Phone</div>
<div class="field" style="left:131px;top:2189px;width:939px;padding-bottom:24px">Message</div>
<span class="outline-btn" style="left:523px;top:2267px;width:155px;height:45px;line-height:41px">SEND</span>

<footer class="abs site-footer">©BRIGHTLINE LABS- 2018. All Rights Reserved.</footer>

</body>
</html>
```